Orvane Group Business Card

Building Management company based in Sydney, Australia. We provide onsite management for commercial and residential buildings.
I would like a sophisticated minimalist design that indicates that we provide a high-end service. I would like a silver or metal look background or something similar.
The business card should have:
Name
Title
email
Office Phone
Mobile
Address
Website
The services that we provide should be prominent:
Building Management - Concierge - Caretaking - Cleaning

```html
<!DOCTYPE html>
<html lang="en">
<head>
<meta charset="utf-8">
<title>Orvane Group Business Card</title>
<link rel="stylesheet" href="https://fonts.googleapis.com/css2?family=Open+Sans:wght@400;600;700;800&display=swap">
<style>
  :root {
    --backdrop: #2b2b2d;
    --card-black: #0d0d0f;
    --card-black-soft: #1e1e21;
    --silver-light: #f4f4f4;
    --silver-mid: #d9d9da;
    --silver-dark: #bdbdbf;
    --brand-blue: #1f6fc4;
    --ink: #1b1b1b;
    --ink-soft: #333;
    --white: #ffffff;
  }
  * { box-sizing: border-box; margin: 0; padding: 0; }
  html, body { width: 1200px; height: 852px; overflow: hidden; }
  body {
    background: var(--backdrop);
    font-family: "Open Sans", Arial, sans-serif;
    position: relative;
  }
  .card {
    position: absolute;
    width: 525px;
    height: 300px;
    border-radius: 22px;
    overflow: hidden;
    top: 276px;
    box-shadow: 0 10px 30px rgba(0,0,0,.45);
  }
  /* Front */
  .card-front {
    left: 50px;
    background: radial-gradient(ellipse at 45% 35%, var(--card-black-soft), var(--card-black) 70%);
  }
  .front-accent {
    position: absolute;
    height: 3px;
    width: 52px;
    background: var(--brand-blue);
  }
  .front-accent.top { right: 70px; top: 92px; }
  .front-accent.bottom { left: 70px; bottom: 46px; }
  .front-mark {
    position: absolute;
    left: 0; right: 0; top: 108px;
    display: flex; justify-content: center; align-items: center; gap: 12px;
  }
  .mark-square {
    width: 22px; height: 22px; background: var(--brand-blue); flex: none;
  }
  .front-name {
    font-weight: 800;
    font-size: 34px;
    letter-spacing: 1px;
    color: var(--silver-mid);
  }
  .front-url {
    position: absolute;
    left: 0; right: 0; top: 180px;
    text-align: center;
    color: var(--silver-mid);
    font-size: 14px;
    letter-spacing: 3px;
  }
  .front-services {
    position: absolute;
    left: 0; right: 0; top: 212px;
    text-align: center;
    color: var(--brand-blue);
    font-size: 11px;
    font-weight: 600;
    letter-spacing: 1.5px;
    text-transform: uppercase;
  }
  /* Back */
  .card-back {
    left: 625px;
    background: linear-gradient(115deg, var(--silver-light) 0%, var(--silver-mid) 35%, var(--silver-light) 55%, var(--silver-dark) 100%);
  }
  .back-divider {
    position: absolute;
    left: 250px; top: 0; bottom: 60px;
    width: 1px;
    background: rgba(0,0,0,.08);
  }
  .back-mark {
    position: absolute;
    left: 28px; top: 124px;
    display: flex; align-items: center; gap: 9px;
  }
  .back-mark .mark-square { width: 16px; height: 16px; }
  .back-name {
    font-weight: 800;
    font-size: 20px;
    color: var(--ink);
    letter-spacing: .5px;
    white-space: nowrap;
  }
  .contact {
    position: absolute;
    left: 272px; top: 36px;
    color: var(--ink-soft);
  }
  .person-name {
    color: var(--brand-blue);
    font-weight: 700;
    font-size: 16px;
  }
  .person-title {
    font-size: 10.5px;
    margin-top: 2px;
    margin-left: 12px;
  }
  .contact-list {
    list-style: none;
    margin-top: 20px;
    font-size: 12px;
    line-height: 16px;
  }
  .contact-list li { display: flex; align-items: flex-start; gap: 8px; }
  .contact-list svg { width: 11px; height: 11px; margin-top: 3px; fill: var(--ink); flex: none; }
  .contact-list .icon-spacer { width: 11px; flex: none; }
  .back-bands { position: absolute; left: 0; bottom: 0; width: 525px; height: 70px; }
  .back-url {
    position: absolute;
    right: 36px; bottom: 22px;
    color: var(--white);
    font-size: 13px;
  }
  .back-url .highlight { color: var(--brand-blue); }
</style>
</head>
<body>
  <section class="card card-front" aria-label="Card front">
    <span class="front-accent top"></span>
    <div class="front-mark">
      <span class="mark-square"></span>
      <span class="front-name">ORVANE GROUP</span>
    </div>
    <p class="front-url">www.orvanegroup.co.uk</p>
    <p class="front-services">Building Management · Concierge · Caretaking · Cleaning</p>
    <span class="front-accent bottom"></span>
  </section>

  <section class="card card-back" aria-label="Card back">
    <span class="back-divider"></span>
    <div class="back-mark">
      <span class="mark-square"></span>
      <span class="back-name">ORVANE GROUP</span>
    </div>
    <div class="contact">
      <p class="person-name">Your Long Name</p>
      <p class="person-title">Managing Director</p>
      <ul class="contact-list">
        <li><span class="icon-spacer"></span>00.00.00.0000</li>
        <li>
          <svg viewBox="0 0 12 12"><path d="M2 1h2l1 3-1.3 1a7 7 0 0 0 3.3 3.3L8 7l3 1v2a1 1 0 0 1-1 1A9 9 0 0 1 1 2a1 1 0 0 1 1-1z"/></svg>
          00.00.00.0000
        </li>
        <li>
          <svg viewBox="0 0 12 12"><path d="M3.5 0h5a1 1 0 0 1 1 1v10a1 1 0 0 1-1 1h-5a1 1 0 0 1-1-1V1a1 1 0 0 1 1-1zm.5 1.5v7.5h4V1.5zM6 9.7a.7.7 0 1 0 0 1.4.7.7 0 0 0 0-1.4z"/></svg>
          yourname@yourwebsite.com
        </li>
        <li>
          <svg viewBox="0 0 12 12"><path d="M1 2.5h10v7H1zm.8.8v.3L6 6.5l4.2-2.9v-.3zm0 1.3v4.1h8.4V4.6L6 7.5z"/></svg>
          <span>Your Commercial or office address<br>in just two line with pincode</span>
        </li>
      </ul>
    </div>
    <svg class="back-bands" viewBox="0 0 525 70" aria-hidden="true">
      <polygon points="0,48 290,38 302,14 525,8 525,70 0,70" fill="#1f6fc4"/>
      <polygon points="318,8 525,8 525,70 300,70" fill="#0d0d0f"/>
    </svg>
    <p class="back-url">www.<span class="highlight">yourwebsite</span>.com</p>
  </section>
</body>
</html>
```